Business Card Design

We need a business card designed for our new company. Prefer a black card with white logo & writing.

Contact Information for Business Card

Ted Galloway, address: 7-4812 Fernhollow Road, Abbotsford, BC, V3K 8R2, Office Phone: 604-712-3390, Cell: 604-947-2164, Email: ted@resinworkshub.ca

Colors

Designer to choose only greyscale colors for use in the design.

```html
<!DOCTYPE html>
<html lang="en">
<head>
<meta charset="utf-8">
<title>Resinworks Hub – Business Card</title>
<link rel="stylesheet" href="https://fonts.googleapis.com/css2?family=Montserrat:wght@400;500;600;700&display=swap">
<style>
  :root {
    --backdrop: #2b2b2b;
    --card: #161616;
    --white: #ffffff;
    --soft-grey: #b9b9b9;
    --band-text: #4a4a4a;
    --seal-light: #6a6a6a;
    --seal-dark: #050505;
  }
  * { margin: 0; padding: 0; box-sizing: border-box; }
  html, body { width: 1200px; height: 1059px; overflow: hidden; }
  body {
    background: var(--backdrop);
    font-family: "Montserrat", sans-serif;
    position: relative;
  }
  .card {
    position: absolute;
    left: 253px;
    width: 694px;
    height: 394px;
    background: var(--card);
    border-radius: 16px;
    overflow: hidden;
  }
  .card--front { top: 88px; }
  .card--back { top: 546px; }

  .seal {
    position: absolute;
    left: 256px; top: 106px;
    width: 182px; height: 182px;
    border-radius: 50%;
    background: radial-gradient(circle at 30% 22%, var(--seal-light) 0%, #1c1c1c 48%, var(--seal-dark) 100%);
    display: flex; align-items: center; justify-content: center;
  }
  .seal__name {
    color: var(--soft-grey);
    font-weight: 600;
    font-size: 15px;
    letter-spacing: 0.5px;
    text-align: center;
    line-height: 1.3;
  }

  .brand {
    position: absolute;
    left: 0; right: 0; top: 94px;
    text-align: center;
    color: var(--white);
    font-weight: 700;
    font-size: 36px;
    letter-spacing: 1px;
  }

  .identity {
    position: absolute;
    right: 368px; top: 244px;
    text-align: right;
    color: var(--white);
  }
  .identity__name { font-weight: 600; font-size: 29px; line-height: 1.1; }
  .identity__title { font-weight: 400; font-size: 17px; margin-top: 6px; }

  .divider {
    position: absolute;
    left: 352px; top: 245px;
    width: 2px; height: 73px;
    background: var(--white);
  }

  .contacts {
    position: absolute;
    left: 376px; top: 241px;
    list-style: none;
    color: var(--white);
    font-size: 17.5px;
    font-weight: 400;
  }
  .contacts li { display: flex; align-items: center; height: 27px; }
  .contacts svg { width: 14px; height: 14px; margin-right: 8px; fill: var(--white); }

  .address-band {
    position: absolute;
    left: 0; right: 0; top: 346px;
    height: 24px;
    background: var(--white);
  }
  .address-band__text {
    position: absolute;
    left: 0; right: 40px; top: 0;
    text-align: center;
    line-height: 24px;
    color: var(--band-text);
    font-size: 16.5px;
  }
  .address-band__dot {
    position: absolute;
    left: 626px; top: 1px;
    width: 22px; height: 22px;
    border-radius: 50%;
    background: #1e1e1e;
  }
</style>
</head>
<body>
  <section class="card card--front">
    <div class="seal"><span class="seal__name">Resinworks<br>Hub</span></div>
  </section>

  <section class="card card--back">
    <div class="brand">RESINWORKS HUB</div>

    <div class="identity">
      <div class="identity__name">Ted Galloway</div>
      <div class="identity__title">Owner/CEO</div>
    </div>

    <div class="divider"></div>

    <ul class="contacts">
      <li>
        <svg viewBox="0 0 24 24"><path d="M3 9c0-3 4-5 9-5s9 2 9 5v2h-5V9c-1-.6-2.5-1-4-1s-3 .4-4 1v2H3z M6 12h12l2 8H4z"/></svg>
        604-712-3390
      </li>
      <li>
        <svg viewBox="0 0 24 24"><path d="M7 1h10a2 2 0 0 1 2 2v18a2 2 0 0 1-2 2H7a2 2 0 0 1-2-2V3a2 2 0 0 1 2-2zm0 3v14h10V4zm5 15.5a1 1 0 1 0 0 2 1 1 0 0 0 0-2z"/></svg>
        604-947-2164
      </li>
      <li>
        <svg viewBox="0 0 24 24"><path d="M2 9l10-7 10 7v13H2zm2 2.2V20h16v-8.8l-8 5.3z"/></svg>
        ted@resinworkshub.ca
      </li>
    </ul>

    <div class="address-band">
      <div class="address-band__text">7-4812 Fernhollow Road, Abbotsford, BC, V3K 8R2</div>
      <div class="address-band__dot"></div>
    </div>
  </section>
</body>
</html>
```